Initial website for sport tech startup

We are currently in the R&D phases of our new product. It’s a headband to prevent concussion in the soccer market initially.

We have 2 products, one that’s basic aimed at the youth market and the other more technology driven that’s aimed at the academies and professional market.

Initially the product will launch in the UK

Target Market(s)

Youth soccer players and parents in UK, Soccer Clubs, Federations.

Industry/Entity Type

Sporting Good

Coding

Coded - Design and coding required

Number of Pages Required

5+ page

Requirements
Must have
• Professional style that can be adapted and changed over the coming months.
Nice to have
• Ecommerce ability in the future.

```html
<!DOCTYPE html>
<html lang="en">
<head>
<meta charset="utf-8">
<title>Haloband – Life is about timing</title>
<link href="https://fonts.googleapis.com/css2?family=Poppins:wght@300;400;500;600;700;800;900&family=Raleway:wght@400;500&display=swap" rel="stylesheet">
<style>
:root{
  --sky:#03a9ec;
  --navy:#04618f;
  --ink:#111418;
  --text:#2b2f36;
  --muted:#7b8088;
  --pale:#eef2f6;
  --blog-bg:#f3f5f8;
  --footer:#2a2a2a;
  --footer-text:#b9bcc0;
  --white:#ffffff;
}
*{margin:0;padding:0;box-sizing:border-box}
html,body{width:1200px;height:3337px;overflow:hidden}
body{position:relative;background:var(--white);font-family:'Poppins',sans-serif;color:var(--text)}
.abs{position:absolute}

/* hero */
.hero{left:0;top:0;width:1200px;height:594px;background:var(--pale)}
.hero-blue{left:0;top:0;width:645px;height:594px;background:var(--sky)}
.hero-gap{left:645px;top:0;width:28px;height:594px;background:var(--white)}
.hero-right{left:673px;top:0;width:527px;height:594px;background:var(--pale)}
.hero-photo{left:470px;top:118px;width:600px;height:520px;border-radius:40% 45% 30% 50%;background:radial-gradient(ellipse at 50% 45%,#e9eef2 0%,#d48a3c 35%,rgba(240,120,30,.55) 55%,rgba(238,242,246,0) 72%)}
.logo{left:117px;top:39px;display:flex;align-items:center;gap:10px;color:var(--white);font-weight:500;font-size:30px;letter-spacing:1px}
.logo .mark{width:14px;height:14px;background:var(--white)}
.nav{left:692px;top:41px;width:332px;height:39px;background:var(--white);border-radius:20px;display:flex;align-items:center;justify-content:space-around;padding:0 20px;font-size:13px;color:#5a5f66}
.nav .active{color:var(--ink);font-weight:500;position:relative}
.nav .active::after{content:"";position:absolute;left:50%;bottom:-8px;width:3px;height:3px;border-radius:50%;background:var(--ink);transform:translateX(-50%)}
.cart{left:1048px;top:48px}
.cart-count{left:1066px;top:42px;width:15px;height:15px;border-radius:50%;background:var(--sky);color:var(--white);font-size:9px;text-align:center;line-height:15px}
.hero-title{left:117px;top:212px;color:var(--white);font-weight:900;font-size:86px;line-height:1;letter-spacing:1px}
.hero-title2{left:117px;top:308px;color:var(--ink);font-weight:900;font-size:50px;line-height:1}
.hero-sub{left:117px;top:374px;width:380px;color:var(--ink);font-weight:600;font-size:15px;line-height:25px}
.btn-outline{left:118px;top:442px;width:139px;height:39px;border:2px solid var(--white);border-radius:20px;color:var(--white);font-size:13px;font-weight:500;text-align:center;line-height:35px}

/* about */
.about-title{left:120px;top:700px;width:480px;font-size:24px;font-weight:600;line-height:37px;color:var(--ink)}
.about-text{left:120px;top:800px;width:480px;font-family:'Raleway',sans-serif;font-size:16px;line-height:30px;color:var(--text)}
.about-text p+p{margin-top:16px}
.frame-big{left:670px;top:680px;width:358px;height:340px;border:2px solid var(--navy)}
.photo-big{left:683px;top:695px;width:333px;height:312px;background:linear-gradient(135deg,#7a8c6a,#27416f 45%,#c9343a 60%,#3b6fc1)}
.frame-small{left:622px;top:907px;width:215px;height:152px;border:2px solid var(--navy);background:var(--white)}
.photo-small{left:629px;top:914px;width:201px;height:138px;background:linear-gradient(180deg,#9fb8c9,#3d7a3a 55%,#2e6a2f)}

/* product info */
.info{left:0;top:1153px;width:1200px;height:525px;background:var(--navy)}
.info-title{left:0;top:1218px;width:1200px;text-align:center;color:var(--white);font-size:30px;font-weight:300}
.info-title b{font-weight:700}
.card{width:223px;height:252px;background:var(--white);border:1px solid #b7d36a;text-align:center;padding-top:36px}
.card h3{font-size:16px;font-weight:600;color:var(--ink);margin:22px 0 14px}
.card p{font-size:13px;color:var(--muted);line-height:22px;padding:0 30px}
.card .go{display:block;width:32px;height:32px;border-radius:50%;background:var(--navy);margin:14px auto 0}

/* headband */
.hb-title{left:0;top:1734px;width:1200px;text-align:center;font-size:32px;font-weight:800;color:var(--ink)}
.hb-line{left:597px;top:1782px;width:1px;height:26px;background:#9aa0a6}
.hb-photo{left:340px;top:1840px;width:502px;height:296px;border-radius:30px 60px 120px 200px;background:linear-gradient(160deg,#5b626b,#3d444c 60%,#23272c)}
.btn-fill{left:531px;top:2131px;width:138px;height:36px;border-radius:18px;background:var(--sky);color:var(--white);font-size:13px;font-weight:500;text-align:center;line-height:36px}
.dots{left:575px;top:2212px;display:flex;gap:9px}
.dots i{width:10px;height:10px;border-radius:50%;background:#c7cbd0}
.dots i.on{background:var(--navy)}

/* blog */
.blog{left:0;top:2278px;width:1200px;height:592px;background:var(--blog-bg)}
.blog-title{left:0;top:2322px;width:1200px;text-align:center;font-size:42px;font-weight:300;color:var(--navy)}
.blog-title b{font-weight:700;color:var(--ink)}
.blog-sub{left:0;top:2382px;width:1200px;text-align:center;font-family:'Raleway',sans-serif;font-size:20px;color:#8a8f96}
.blog-img{width:411px;height:245px}
.img-a{left:146px;top:2445px;background:linear-gradient(120deg,#3a4a5e,#8797a8 50%,#dfe3e6)}
.img-b{left:618px;top:2445px;background:linear-gradient(120deg,#8c1f24,#5f6d3d 55%,#c9d2b8)}
.blog-card{width:289px;height:88px;background:var(--white);box-shadow:0 4px 14px rgba(0,0,0,.06);padding:14px 18px}
.blog-card p{font-size:11px;font-weight:500;color:var(--ink);line-height:19px;width:210px}
.blog-card span{display:flex;align-items:center;gap:10px;font-size:12px;color:var(--muted);margin-top:4px}
.blog-card span::before{content:"";width:24px;height:2px;background:#3dbb6e}
.blog-card.grey span::before{background:#c8ccd0}
.blog-card .arrow{position:absolute;right:18px;top:35px;width:28px;height:28px;border:1px solid #dde0e3;border-radius:50%}
.btn-view{left:520px;top:2764px;width:160px;height:36px;border:2px solid #8c9197;border-radius:18px;font-size:13px;font-weight:500;text-align:center;line-height:32px;color:var(--text)}

/* newsletter */
.news-title{left:0;top:2920px;width:1200px;text-align:center;font-size:32px;font-weight:400;color:var(--ink)}
.news-field{left:259px;top:3004px;width:677px;height:22px;border-bottom:1px solid #d5d8dc;display:flex;justify-content:space-between;font-size:10px;color:#a9adb2}

/* footer */
.footer{left:0;top:3087px;width:1200px;height:250px;background:var(--footer)}
.f-col{color:var(--footer-text);font-size:13px}
.f-col h4{color:#e6e7e8;font-weight:400;font-size:15px;margin-bottom:24px}
.f-col li{list-style:none;margin-bottom:10px}
.f-sep{width:1px;height:140px;background:#3c3c3c}
.f-logo{left:852px;top:3178px;display:flex;align-items:center;gap:10px;color:var(--white);font-weight:500;font-size:28px;letter-spacing:1px}
.f-logo .mark{width:12px;height:12px;background:var(--white)}
.social{left:870px;top:3233px;display:flex;gap:16px}
.social i{width:12px;height:12px;border-radius:50%;background:#9a9da1}
</style>
</head>
<body>

<!-- hero -->
<div class="abs hero"></div>
<div class="abs hero-blue"></div>
<div class="abs hero-gap"></div>
<div class="abs hero-right"></div>
<div class="abs hero-photo" role="img" aria-label="Footballer mid-air kicking a ball, with orange and yellow shards around him"></div>
<div class="abs logo"><span>HALOBAND</span><span class="mark"></span></div>
<nav class="abs nav"><span class="active">Home</span><span>Products</span><span>Shop</span><span>Contact</span></nav>
<svg class="abs cart" width="26" height="24" viewBox="0 0 26 24" fill="none" stroke="#6b7078" stroke-width="1.6"><path d="M1 2h4l3 13h13l3-9H7"/><circle cx="10" cy="20" r="1.6"/><circle cx="19" cy="20" r="1.6"/></svg>
<div class="abs cart-count">0</div>
<div class="abs hero-title">LIFE IS</div>
<div class="abs hero-title2">ABOUT TIMING</div>
<div class="abs hero-sub">HALOBAND – BRINGING SAFETY TO THE SPORTS CONCUSSION DEBATE</div>
<div class="abs btn-outline">Learn More</div>

<!-- about -->
<h2 class="abs about-title">HALOBAND – BRINGING SAFETY TO THE SPORTS CONCUSSION DEBATE</h2>
<div class="abs about-text">
  <p>Haloband is designing and developing head protectioHaloband protection products to reduce the likelihood of concussion when playing sports.</p>
  <p>Exploring and understanding medical insights, material science and composites research, current and former players experiences and governing bodies guidelines has allowed Haloband to develop the safety</p>
</div>
<div class="abs frame-big"></div>
<div class="abs photo-big" role="img" aria-label="Two footballers challenging for a header"></div>
<div class="abs frame-small"></div>
<div class="abs photo-small" role="img" aria-label="Player receiving attention on the pitch"></div>

<!-- product info -->
<div class="abs info"></div>
<h2 class="abs info-title">Product <b>Info</b></h2>
<div class="abs card" style="left:240px;top:1304px">
  <svg width="48" height="52" viewBox="0 0 48 52" fill="none" stroke="#1f5f8f" stroke-width="1.6"><rect x="8" y="3" width="32" height="40" rx="3"/><path d="M14 12h20M14 18h20M14 24h14"/><path d="M4 38l6 8 14-16"/></svg>
  <h3>Safety Tested</h3>
  <p>Lorem Ipsum is simply dummy text of the</p>
</div>
<div class="abs card" style="left:489px;top:1308px;padding-top:30px">
  <svg width="52" height="46" viewBox="0 0 52 46" fill="none" stroke="#1f5f8f" stroke-width="1.6"><path d="M6 28C14 8 34 4 46 4 42 18 30 28 10 30"/><path d="M6 36l20-20"/><path d="M2 42h48" stroke-dasharray="4 3"/></svg>
  <h3 style="margin-top:14px">Light Weight</h3>
  <p>Lorem Ipsum is simply dummy text of the</p>
  <svg class="go" viewBox="0 0 32 32"><circle cx="16" cy="16" r="16" fill="#04618f"/><path d="M10 16h12M17 11l5 5-5 5" stroke="#fff" stroke-width="1.6" fill="none"/></svg>
</div>
<div class="abs card" style="left:737px;top:1304px">
  <svg width="54" height="52" viewBox="0 0 54 52" fill="none" stroke="#1f5f8f" stroke-width="1.6"><rect x="10" y="10" width="26" height="24" rx="8"/><path d="M4 30h38v10H4zM8 40v6M38 40v6M46 4v42M44 4h6"/><path d="M18 22h10M23 17v10"/></svg>
  <h3>Comfortable</h3>
  <p>Lorem Ipsum is simply dummy text of the</p>
</div>

<!-- headband -->
<h2 class="abs hb-title">Headband</h2>
<div class="abs hb-line"></div>
<div class="abs hb-photo" role="img" aria-label="Grey padded protective headband product"></div>
<div class="abs btn-fill">Shop Now</div>
<div class="abs dots"><i></i><i class="on"></i><i></i></div>

<!-- blog -->
<div class="abs blog"></div>
<h2 class="abs blog-title">Our <b>Blog</b></h2>
<p class="abs blog-sub">Lorem Ipsum is simply dummy text of the printing</p>
<div class="abs blog-img img-a" role="img" aria-label="Goalkeeper diving for a ball in a stadium"></div>
<div class="abs blog-img img-b" role="img" aria-label="Player's boot resting on a football"></div>
<div class="abs blog-card" style="left:293px;top:2635px">
  <p>Lorem Ipsum is simply dummy text of the printing and typesetting</p>
  <span>Headband</span>
  <svg class="arrow" viewBox="0 0 28 28"><path d="M12 9l5 5-5 5" stroke="#3dbb6e" stroke-width="1.4" fill="none"/></svg>
</div>
<div class="abs blog-card grey" style="left:765px;top:2637px">
  <p>Lorem Ipsum is simply dummy text of the printing and typesetting</p>
  <span>Headband</span>
  <svg class="arrow" viewBox="0 0 28 28"><path d="M12 9l5 5-5 5" stroke="#9aa0a6" stroke-width="1.4" fill="none"/></svg>
</div>
<div class="abs btn-view">View More</div>

<!-- newsletter -->
<h2 class="abs news-title">Join Our Newsletter</h2>
<div class="abs news-field"><span>Your email address</span><span>Subscribe</span></div>

<!-- footer -->
<footer class="abs footer"></footer>
<div class="abs f-col" style="left:154px;top:3130px">
  <h4>Contact Us</h4>
  <p style="line-height:23px">Lorem Ipsum, is simply<br>dummy text of the</p>
  <p style="margin-top:22px">+xxx xxxx xxxxx</p>
  <p style="margin-top:18px">xxxxxxx@mailbox.net</p>
</div>
<div class="abs f-sep" style="left:402px;top:3138px"></div>
<div class="abs f-col" style="left:530px;top:3130px">
  <h4>Contact Us</h4>
  <ul><li>Home</li><li>About</li><li>Shop</li><li>Contact</li></ul>
</div>
<div class="abs f-sep" style="left:733px;top:3138px"></div>
<div class="abs f-logo"><span>HALOBAND</span><span class="mark"></span></div>
<div class="abs social"><i></i><i></i><i></i><i></i><i></i></div>

</body>
</html>
```